Lindqvar Foundation Letterhead

We are a newly established non profit registered in Maryland but operates in Africa, south of the sahara. We offer scholarships to deserving young adults from high school through college. Our color theme for our existing logo is purple, we want a design that is stylish, spellbinding yet a letterhead that projects seriousness. More information on www.thelindqvarfoundation.example

Target Market(s)

High school and college students in sub saharan African as well as our donors in the US

Industry/Entity Type

Non Profit

Font styles to use
Script

Requirements
Must have
• Logo at the top and if possible watermark the logo in the middle of the letterhead, contact address,
Should not have
• NA

```html
<!DOCTYPE html>
<html lang="en">
<head>
<meta charset="utf-8">
<title>Lindqvar Foundation Letterhead</title>
<link rel="stylesheet" href="https://fonts.googleapis.com/css2?family=Cabin:wght@400;500&family=Cormorant+SC:wght@600&display=swap">
<style>
  :root {
    --backdrop: #c9c9cb;
    --paper: #ffffff;
    --purple-deep: #4f2a8c;
    --purple-mid: #7a3fa6;
    --purple-soft: #a890c8;
    --lavender: #d4d0e0;
    --ink: #2b2b2f;
    --ink-soft: #55555c;
  }
  * { box-sizing: border-box; margin: 0; padding: 0; }
  html, body {
    width: 1200px; height: 795px; overflow: hidden;
    background: var(--backdrop);
  }
  .letterhead {
    position: absolute; left: 330px; top: 16px;
    width: 540px; height: 763px;
    background: var(--paper);
    font-family: "Cabin", "Gill Sans", sans-serif;
    color: var(--ink);
    overflow: hidden;
    box-shadow: 0 2px 8px rgba(0,0,0,.18);
  }
  .brand {
    position: absolute; left: 42px; top: 130px;
    display: flex; align-items: center; gap: 8px;
  }
  .brand-dot {
    width: 22px; height: 22px; border-radius: 50%;
    background: var(--purple-mid);
  }
  .brand-name {
    font-size: 15px; font-weight: 500; color: var(--purple-mid);
    letter-spacing: .02em;
  }
  .sender {
    position: absolute; right: 40px; top: 38px; text-align: right;
  }
  .sender-name {
    font-family: "Cormorant SC", "Times New Roman", serif;
    font-weight: 600; font-size: 16px; color: var(--purple-deep);
    letter-spacing: .04em; margin-bottom: 3px;
  }
  .sender-line { font-size: 9px; line-height: 1.4; color: var(--ink-soft); }
  .letter {
    position: absolute; left: 42px; top: 235px; width: 400px;
    font-size: 9.6px; line-height: 1.45;
  }
  .salutation { font-size: 11px; margin-bottom: 9px; }
  .letter p { margin-bottom: 10px; }
  .sign-off { margin-top: 26px; font-size: 10px; color: var(--ink-soft); }
  .signature {
    width: 80px; height: 26px; margin: 6px 0 4px;
    background: linear-gradient(90deg, rgba(43,43,47,.25), rgba(43,43,47,.06));
    border-radius: 3px;
  }
  .signer { font-size: 10px; line-height: 1.35; color: var(--ink-soft); }
  .mark-accent {
    position: absolute; right: 26px; top: 452px;
    width: 130px; height: 130px; border-radius: 50%;
    background: radial-gradient(circle at 40% 40%, var(--purple-soft), var(--purple-mid));
    opacity: .85;
  }
  .footer { position: absolute; left: 0; right: 0; bottom: 0; height: 150px; }
  .footer-web {
    position: absolute; right: 22px; top: 2px;
    font-size: 11px; color: var(--purple-mid); letter-spacing: .02em;
  }
  .footer svg { position: absolute; left: 0; bottom: 0; }
</style>
</head>
<body>
  <main class="letterhead">
    <div class="brand">
      <span class="brand-dot"></span>
      <span class="brand-name">Lindqvar Foundation Inc</span>
    </div>

    <header class="sender">
      <div class="sender-name">The Lindqvar Foundation Inc</div>
      <div class="sender-line">12 Harrow Glen Court,</div>
      <div class="sender-line">Suite 3, Ellicott City, MD 21043</div>
      <div class="sender-line">admin@thelindqvarfoundation.example</div>
    </header>

    <section class="letter">
      <div class="salutation">Dear Mr. John,</div>
      <p>Lorem Ipsum is simply dummy text of the printing and typesetting industry. Lorem Ipsum has been the industry's standard dummy text ever since the 1500s, when an unknown printer took a galley of type and scrambled it to make a type specimen book. It has survived not only five centuries, but also the leap into electronic typesetting, remaining essentially unchanged.</p>
      <p>The standard chunk of Lorem Ipsum used since the 1500s is reproduced below for those interested. Sections 1.10.32 and 1.10.33 from "de Finibus Bonorum et Malorum" by Cicero are also reproduced in their exact original form, accompanied by English versions from the 1914 translation by H. Rackham.</p>
      <p>Lorem Ipsum is simply dummy text of the printing and typesetting industry. Lorem Ipsum has been the industry's standard dummy text ever since the 1500s, when an unknown printer took a galley of type and scrambled it to make a type specimen book. It has survived not only five centuries, but also the leap into electronic typesetting, remaining essentially unchanged. It was popularised in the</p>
      <div class="sign-off">Sincerely Your,</div>
      <div class="signature" role="img" aria-label="Handwritten signature"></div>
      <div class="signer">Name Last Name<br>Company Name</div>
    </section>

    <div class="mark-accent"></div>

    <footer class="footer">
      <div class="footer-web">www.thelindqvarfoundation.example</div>
      <svg width="540" height="132" viewBox="0 0 540 132" aria-hidden="true">
        <defs>
          <linearGradient id="band" x1="0" x2="1">
            <stop offset="0" stop-color="#4f2a8c"/>
            <stop offset=".55" stop-color="#7a3fa6"/>
            <stop offset="1" stop-color="#4f2a8c"/>
          </linearGradient>
        </defs>
        <rect x="0" y="0" width="540" height="8" fill="var(--lavender)"/>
        <rect x="0" y="12" width="540" height="120" fill="url(#band)"/>
      </svg>
    </footer>
  </main>
</body>
</html>
```